We need a card and logo design for a new business based in Dallas Texas called Stonemarsh Financial LLC.

We provide bridge loans.We offer pay day loans,title loans and check cashing.Our products are emmergency loans that help borrowers meet short term liquidity needs until the next pay check.

The final design should communicate,professionalism,Sophistication and friendliness to our customers.Use the color Blue as much as possible and another eye catching color if possible.We will consider a profesional looking knight logo with the color Blue in it.Please design a full corporate identity.

```html
<!DOCTYPE html>
<html lang="en">
<head>
<meta charset="utf-8">
<title>Stonemarsh Financial LLC – Business Card</title>
<link rel="stylesheet" href="https://fonts.googleapis.com/css2?family=Open+Sans:wght@400;600;700&display=swap">
<style>
  :root {
    --backdrop: #34302e;
    --card-white: #ffffff;
    --navy: #2b2a78;
    --accent-red: #d0202a;
    --ink: #1e1e1e;
    --divider: #8a8a8a;
    --back-dark: #121314;
    --back-glow: #4a4d4f;
    --back-text: #f2f2f2;
  }
  * { margin: 0; padding: 0; box-sizing: border-box; }
  html, body {
    width: 1000px; height: 1200px; overflow: hidden;
    background: var(--backdrop);
    font-family: "Open Sans", Arial, sans-serif;
  }
  .canvas { position: relative; width: 1000px; height: 1200px; }

  .card {
    position: absolute;
    width: 723px; height: 423px;
  }
  .card-front { left: 140px; top: 119px; background: var(--card-white); }
  .card-back {
    left: 125px; top: 638px;
    background: radial-gradient(ellipse 60% 65% at 50% 42%, var(--back-glow) 0%, #2a2c2d 50%, var(--back-dark) 100%);
  }

  .wordmark {
    position: absolute; left: 0; right: 0;
    display: flex; align-items: center; justify-content: center; gap: 12px;
    font-weight: 700; font-size: 30px; letter-spacing: 2px;
    text-transform: uppercase;
  }
  .wordmark-dot { width: 16px; height: 16px; border-radius: 50%; }
  .card-front .wordmark { top: 100px; color: var(--navy); }
  .card-front .wordmark-dot { background: var(--accent-red); }
  .card-back .wordmark { top: 195px; color: var(--back-text); }
  .card-back .wordmark-dot { background: var(--accent-red); }

  .contact-person { position: absolute; left: 35px; top: 259px; color: var(--ink); }
  .person-name {
    font-weight: 700; font-size: 18px; letter-spacing: 1.5px;
    color: var(--navy); text-transform: uppercase; line-height: 24px;
  }
  .person-role { font-size: 16px; line-height: 20px; }
  .person-email { font-size: 16px; margin-top: 11px; }

  .divider {
    position: absolute; left: 361px; top: 249px;
    width: 1.5px; height: 131px; background: var(--divider);
  }

  .contact-office {
    position: absolute; right: 35px; top: 260px;
    text-align: right; font-size: 16px; color: var(--ink); line-height: 23px;
  }
  .office-phone { margin-bottom: 5px; }
  .office-address { margin-top: 14px; }
</style>
</head>
<body>
<main class="canvas">
  <section class="card card-front" aria-label="Card front">
    <div class="wordmark"><span class="wordmark-dot"></span><span>Stonemarsh Financial LLC</span></div>

    <div class="contact-person">
      <p class="person-name">Daniel Reyes</p>
      <p class="person-role">Financial Advisor</p>
      <p class="person-email">Email: info@stonemarshfinancial.com</p>
    </div>

    <div class="divider"></div>

    <div class="contact-office">
      <p class="office-phone">Tel: 111-123-4567</p>
      <p>Fax: 111-123-4567</p>
      <p class="office-address">XXX Some Street Address<br>State, Country</p>
    </div>
  </section>

  <section class="card card-back" aria-label="Card back">
    <div class="wordmark"><span class="wordmark-dot"></span><span>Stonemarsh Financial LLC</span></div>
  </section>
</main>
</body>
</html>
```